Local Roofing/Construction company business needs new biz card design

We need a new business card design, current cards are from the start of this operation and generic at best. We are a local Construction Company (General Contractor) with a majority of our work originating from insurance claims-exterior finish work is the main focus (Roofs-Siding-Gutters etc). Heavily involved with homeowners and the low ball offers they receive from insurance company's after a insurable event takes place. I have attached some of our original logo file(s) below.

```html
<!DOCTYPE html>
<html lang="en">
<head>
<meta charset="utf-8">
<title>Stonebay Construction — Business Card</title>
<link rel="stylesheet" href="https://fonts.googleapis.com/css2?family=Montserrat:wght@400;500;700;800&display=swap">
<style>
  :root {
    --page-bg: #1c1e20;
    --card-bg: #0e1c20;
    --pattern-bg: #10262b;
    --brand-green: #55b96a;
    --text-light: #f2f4f3;
    --divider: #3f8a50;
  }
  * { box-sizing: border-box; margin: 0; padding: 0; }
  html, body {
    width: 1200px; height: 900px; overflow: hidden;
    background: var(--page-bg);
    font-family: "Montserrat", sans-serif;
  }
  .canvas {
    width: 1200px; height: 900px;
    display: flex; flex-direction: column; align-items: center; justify-content: center;
    gap: 40px;
  }
  .card {
    position: relative;
    width: 700px; height: 400px;
    border-radius: 26px;
    overflow: hidden;
    background: var(--card-bg);
    box-shadow: 0 14px 30px rgba(0,0,0,.45);
  }
  /* Front */
  .card-front .accent-band {
    position: absolute; left: 0; right: 0; bottom: 0; height: 16px;
    background: var(--brand-green);
  }
  .brand {
    position: absolute; left: 48px; top: 120px;
    display: flex; align-items: center; gap: 14px;
  }
  .brand-square {
    width: 34px; height: 34px; background: var(--brand-green); border-radius: 4px;
  }
  .brand-name {
    font-weight: 800; font-size: 26px; letter-spacing: 1px;
    color: var(--brand-green); text-transform: uppercase; line-height: 1.15;
  }
  .divider {
    position: absolute; left: 350px; top: 90px; width: 1px; height: 210px;
    background: var(--divider);
  }
  .details {
    position: absolute; left: 380px; top: 110px; color: var(--text-light);
  }
  .person-name {
    font-weight: 800; font-size: 24px; letter-spacing: 2px;
    color: var(--brand-green); text-transform: uppercase;
  }
  .person-title { font-size: 15px; font-weight: 500; margin: 2px 0 14px; }
  .contact-list { list-style: none; font-size: 14px; font-weight: 500; }
  .contact-item { display: flex; align-items: center; gap: 9px; margin-bottom: 7px; }
  .contact-icon { width: 13px; height: 13px; fill: var(--brand-green); flex: none; }
  .web-mid { color: var(--brand-green); }
  .address { font-size: 14px; font-weight: 500; line-height: 1.5; margin-top: 8px; }
  /* Back */
  .card-back { background: var(--pattern-bg); }
  .back-pattern {
    position: absolute; inset: 0;
    background: linear-gradient(135deg, #12292e 0%, #0f2428 100%);
  }
  .back-brand {
    position: absolute; right: 40px; bottom: 34px;
    display: flex; align-items: center; gap: 8px;
  }
  .back-brand .brand-square { width: 14px; height: 14px; border-radius: 2px; }
  .back-brand-name {
    font-weight: 800; font-size: 14px; color: var(--brand-green);
    text-transform: uppercase; letter-spacing: 1px;
  }
</style>
</head>
<body>
<main class="canvas">
  <section class="card card-front">
    <div class="brand">
      <span class="brand-square"></span>
      <span class="brand-name">Stonebay<br>Construction</span>
    </div>
    <div class="divider"></div>
    <div class="details">
      <h1 class="person-name">Declan Marsh</h1>
      <p class="person-title">Managing Director</p>
      <ul class="contact-list">
        <li class="contact-item">
          <svg class="contact-icon" viewBox="0 0 24 24"><path d="M6.6 10.8a15.1 15.1 0 0 0 6.6 6.6l2.2-2.2a1 1 0 0 1 1-.25 11.4 11.4 0 0 0 3.6.57 1 1 0 0 1 1 1V20a1 1 0 0 1-1 1A17 17 0 0 1 3 4a1 1 0 0 1 1-1h3.5a1 1 0 0 1 1 1c0 1.25.2 2.45.57 3.57a1 1 0 0 1-.25 1z"/></svg>
          0400 555 219
        </li>
        <li class="contact-item">
          <svg class="contact-icon" viewBox="0 0 24 24"><path d="M2 5h20v14H2z M3.5 6.5 12 13l8.5-6.5" fill="none" stroke="#55b96a" stroke-width="2"/></svg>
          info@stonebaybuild.com
        </li>
        <li class="contact-item">
          <svg class="contact-icon" viewBox="0 0 24 24"><circle cx="12" cy="12" r="9" fill="none" stroke="#55b96a" stroke-width="2"/><path d="M3 12h18M12 3c3 3 3 15 0 18M12 3c-3 3-3 15 0 18" fill="none" stroke="#55b96a" stroke-width="1.6"/></svg>
          <span>www.<span class="web-mid">stonebaybuild</span>.com</span>
        </li>
      </ul>
      <p class="address">1450 W Harlow Street<br>Brenton County Name 5120</p>
    </div>
    <div class="accent-band"></div>
  </section>

  <section class="card card-back">
    <div class="back-pattern" role="img" aria-label="Repeating faint brand pattern across the card back"></div>
    <div class="back-brand">
      <span class="brand-square"></span>
      <span class="back-brand-name">Stonebay Construction</span>
    </div>
  </section>
</main>
</body>
</html>
```